New business card/stationary for a consulting company

I am looking for a clean and very professional looking business card for my consulting company as well as corresponding stationary. I am uploading our logo. I like simple and powerful for the feel. No graphics but I am open on everything else. Below is my contact information but would like the final to be in a version I can add my employees information into and print. Thank you.

Daniel Whitcombe
dan@ferncliffadvisory.com
2870 North 9th Avenue, Summit Floor, Elm Ridge, Illinois 60531
www.ferncliffadvisory.com

Industry/Entity Type

Consulting

Contact Information for Business Card

Daniel Whitcombe
dan@ferncliffadvisory.com
www.ferncliffadvisory.com

Font styles to use
Serif
Sans Serif

Requirements
Must have
• Our logo and the business card details.
Nice to have
• our website www.ferncliffadvisory.com

```html
<!DOCTYPE html>
<html lang="en">
<head>
<meta charset="utf-8">
<title>Ferncliff Advisory – Business Card</title>
<link rel="stylesheet" href="https://fonts.googleapis.com/css2?family=Open+Sans:wght@400;700&family=Questrial&display=swap">
<style>
  :root {
    --backdrop: #4a413c;
    --card: #121212;
    --card-edge: #1d1d1d;
    --ink: #f2f2f2;
    --ink-soft: #bdbdbd;
    --logo-grey: #a9a9a9;
  }
  * { margin: 0; padding: 0; box-sizing: border-box; }
  html, body {
    width: 1200px; height: 864px; overflow: hidden;
    background: var(--backdrop);
  }
  .canvas { position: relative; width: 1200px; height: 864px; }

  .card {
    position: absolute;
    width: 560px; height: 320px;
    background: var(--card);
    border: 1px solid var(--card-edge);
    box-shadow: 0 18px 40px rgba(0,0,0,.45);
  }

  /* Front */
  .card--front { left: 60px; top: 80px; }
  .front-mark {
    position: absolute; left: 0; right: 0; top: 100px;
    display: flex; align-items: center; justify-content: center; gap: 14px;
  }
  .front-mark .square { width: 26px; height: 26px; background: var(--logo-grey); }
  .front-mark .name {
    font-family: "Questrial", sans-serif; font-size: 28px;
    letter-spacing: 3px; color: var(--logo-grey); text-transform: uppercase;
  }
  .front-web {
    position: absolute; left: 0; right: 0; top: 200px; text-align: center;
    font-family: "Open Sans", sans-serif; font-size: 13px;
    letter-spacing: 7px; color: var(--ink-soft);
  }

  /* Back */
  .card--back { left: 580px; top: 464px; }
  .back-mark {
    position: absolute; left: 0; right: 0; top: 52px;
    display: flex; align-items: center; justify-content: center; gap: 12px;
  }
  .back-mark .square { width: 18px; height: 18px; background: var(--ink); }
  .back-mark .name {
    font-family: "Questrial", sans-serif; font-size: 22px;
    letter-spacing: 2px; color: var(--ink); text-transform: uppercase;
  }
  .holder {
    position: absolute; right: 318px; top: 150px;
    font-family: "Open Sans", sans-serif; font-weight: 700; font-size: 17px;
    color: var(--ink); text-transform: uppercase; letter-spacing: .3px;
  }
  .divider {
    position: absolute; left: 262px; top: 128px; width: 1px; height: 140px;
    background: var(--ink-soft);
  }
  .contact {
    position: absolute; left: 282px; top: 132px;
    font-family: "Open Sans", sans-serif; font-size: 13.5px; line-height: 19px;
    color: var(--ink); list-style: none;
  }
  .contact .row { display: flex; align-items: center; gap: 8px; }
  .contact .icon { width: 12px; height: 12px; flex: none; }
  .contact .plain { padding-left: 20px; }
</style>
</head>
<body>
<main class="canvas">

  <section class="card card--front" aria-label="Card front">
    <div class="front-mark">
      <span class="square"></span>
      <span class="name">Ferncliff Advisory</span>
    </div>
    <p class="front-web">www.ferncliffadvisory.com</p>
  </section>

  <section class="card card--back" aria-label="Card back">
    <div class="back-mark">
      <span class="square"></span>
      <span class="name">Ferncliff Advisory</span>
    </div>

    <p class="holder">Daniel Whitcombe</p>
    <span class="divider"></span>

    <ul class="contact">
      <li class="plain">2870 North 9th Avenue</li>
      <li class="plain">Summit Floor, Elm Ridge</li>
      <li class="plain">Illinois 60531</li>
      <li class="row">
        <svg class="icon" viewBox="0 0 12 12" aria-hidden="true">
          <rect x="0.5" y="2" width="11" height="8" fill="#f2f2f2"/>
          <path d="M0.5 2 L6 6.5 L11.5 2" stroke="#121212" stroke-width="1.2" fill="none"/>
        </svg>
        dan@ferncliffadvisory.com
      </li>
      <li class="row">
        <svg class="icon" viewBox="0 0 12 12" aria-hidden="true">
          <circle cx="6" cy="6" r="5.5" fill="#f2f2f2"/>
          <ellipse cx="6" cy="6" rx="2.2" ry="5.5" stroke="#121212" stroke-width="1" fill="none"/>
          <line x1="0.5" y1="6" x2="11.5" y2="6" stroke="#121212" stroke-width="1"/>
        </svg>
        www.ferncliffadvisory.com
      </li>
    </ul>
  </section>

</main>
</body>
</html>
```